Brovanek Data Yellow rose letterhead

I have a new logo for my company but in its current form it is too large to be used on letterhead or as a email signature. I need to have the designer use elements from the current logo and create something close to the original but more suited for smaller items.
Updates

I just uploaded a copy of our logo that does not have the weathered affect. Thanks

Reason: More time for revisions

Industry/Entity Type

It Company

Requirements
Must have
• The design must maintain the visual effect of the current logo. It needs to include the yellow rose and the name of the company.
Nice to have
• It would be nice to maintain the stamp theme and incorporate my name, address, phone, email. etc.

```html
<!DOCTYPE html>
<html lang="en">
<head>
<meta charset="utf-8">
<title>Brovanek Data Stationery</title>
<link href="https://fonts.googleapis.com/css2?family=Open+Sans:ital,wght@0,400;0,700;1,400&family=Over+the+Rainbow&display=swap" rel="stylesheet">
<style>
  :root {
    --backdrop: #e9e9e9;
    --paper: #f1f1f1;
    --brown: #59493f;
    --gold: #e3b41f;
    --ink: #3d3d3d;
    --body: #555555;
    --muted: #8a8a8a;
    --white: #ffffff;
  }
  * { box-sizing: border-box; margin: 0; padding: 0; }
  html, body { width: 1200px; height: 900px; overflow: hidden; }
  body {
    background: var(--backdrop);
    font-family: "Open Sans", Arial, sans-serif;
    color: var(--ink);
    position: relative;
  }

  /* Letterhead */
  .letterhead {
    position: absolute; left: 85px; top: 110px; width: 505px; height: 682px;
    background: var(--paper); overflow: hidden;
  }
  .brand-mark {
    position: absolute; display: flex; align-items: center; gap: 5px;
    font-weight: 700; color: var(--brown); font-size: 11px; line-height: 1.15;
  }
  .brand-mark .mark-square {
    width: 14px; height: 14px; background: var(--gold); flex: none;
  }
  .letterhead .brand-mark { left: 14px; top: 30px; width: 100px; }
  .sender {
    position: absolute; left: 122px; top: 10px;
    font-style: italic; color: var(--muted); font-size: 8.6px; line-height: 11px;
  }
  .sender .sender-name { font-size: 11px; line-height: 14px; color: var(--ink); }
  .sender .sender-email { margin-top: 11px; }
  .tagline-band {
    position: absolute; left: 0; top: 92px; width: 505px; height: 24px;
    background: var(--brown); border-top: 1px solid var(--gold);
    color: var(--white); font-size: 8.4px; font-weight: 700;
    padding: 6px 0 0 122px; white-space: nowrap;
  }
  .tagline-band::before {
    content: ""; position: absolute; left: 108px; top: 0; width: 1px; height: 23px;
    background: var(--gold);
  }
  .letter-body {
    position: absolute; left: 121px; top: 159px; width: 299px;
    font-size: 7px; line-height: 10.6px; text-align: justify; color: var(--body);
  }
  .recipient { font-style: italic; line-height: 11.5px; margin-bottom: 18px; font-size: 7.4px; }
  .recipient .recipient-name { font-size: 8px; color: var(--ink); }
  .letter-body p { margin-bottom: 10.6px; }
  .letter-body .closing { margin-top: 20px; margin-bottom: 4px; }
  .signature {
    font-family: "Over the Rainbow", cursive; font-size: 20px; line-height: 28px;
    color: var(--ink); margin-bottom: 4px;
  }
  .letter-footer { position: absolute; left: 0; bottom: 0; width: 505px; height: 225px; }

  /* Envelope back */
  .envelope-back {
    position: absolute; left: 638px; top: 127px; width: 537px; height: 253px;
    background: var(--paper);
  }
  .envelope-flap { position: absolute; left: 0; top: 0; width: 537px; height: 90px; }
  .envelope-back .seal {
    position: absolute; left: 224px; top: 17px; width: 78px; height: 60px;
    background: var(--paper); border: 2px solid var(--gold);
    display: flex; align-items: center; justify-content: center;
  }
  .seal .brand-mark { position: static; font-size: 9px; width: 70px; gap: 3px; }
  .seal .mark-square { width: 9px; height: 9px; }

  /* Envelope front */
  .envelope-front {
    position: absolute; left: 638px; top: 467px; width: 535px; height: 262px;
    background: var(--paper);
  }
  .front-stripes { position: absolute; left: 0; top: 0; width: 535px; }
  .envelope-front .brand-mark { left: 30px; top: 44px; width: 90px; }
  .envelope-front .sender { left: 132px; top: 35px; font-size: 8.3px; line-height: 10.5px; }
  .envelope-front .sender .sender-name { font-size: 10px; color: var(--muted); }
  .envelope-front .sender .sender-email { margin-top: 9px; }
  .envelope-front .divider {
    position: absolute; left: 120px; top: 30px; width: 1px; height: 68px; background: #dcdcdc;
  }
</style>
</head>
<body>

<section class="letterhead">
  <div class="brand-mark"><span class="mark-square"></span><span>Brovanek Data</span></div>
  <div class="sender">
    <div class="sender-name">Dr. Marla Quenby</div>
    <div>418 Cedar Hollow Road, Ste. 1207</div>
    <div>Pinecrest, TX 76510</div>
    <div>(800) 555-0147</div>
    <div class="sender-email">marla@brovanek-data.com</div>
  </div>
  <div class="tagline-band">CLEAR DATA FOUNDATIONS:&nbsp; Building Dependable Insight for Growing Businesses</div>

  <div class="letter-body">
    <div class="recipient">
      <div class="recipient-name">Dana Wexler</div>
      <div>Brightframe Creative Services</div>
      <div>817-555-0163</div>
    </div>
    <p>Dear Marla,<br>This text will be replaced by your own text. It has been a pleasure working with you. You are a rare and excellent communicator! I would love to talk to you about designing your business cards and web site. Psed diam nonummy nibh euismod tincidunt ut laoreet dolore magna aliquam erat volutpat. Ut wisi enim ad minim veniam, quis nostrud exerci tation ullamcorper suscipit lobortis nisl ut aliquip ex ea commodo consequat. Duis autem vel eum iriure dolor in hendrerit in vulputate velit esse molestie consequat, vel illum dolore eu feugiat nulla facilisis at vero eros et accumsan et iusto odio dignissim qui blandit praesent luptatum zzril delenit augue duis dolore te feugait nulla facilisi.</p>
    <p>Ut wisi enim ad minim veniam, quis nostrud exerci tation ullamcorper suscipit lobortis nisl ut aliquip ex ea commodo consequat. Duis autem vel eum iriure dolor in hendrerit in vulputate velit esse molestie consequat, vel illum dolore eu feugiat nulla facilisis at vero eros et accumsan et iusto odio dignissim qui blandit praesent luptatum zzril delenit augue duis dolore te feugait nulla facilisi. Lorem ipsum dolor sit amet, consectetuer adipiscing elit, sed diam nonummy nibh euismod tincidunt ut laoreet dolore magna aliquam erat volutpat.</p>
    <p>Duis autem vel eum iriure dolor in hendrerit in vulputate velit esse molestie consequat, vel illum dolore eu feugiat nulla facilisis at vero eros et accumsan et iusto odio dignissim qui blandit praesent luptatum zzril delenit augue duis dolore te feugait nulla facilisi. Lorem ipsum dolor sit amet, consectetuer adipiscing elit, sed diam nonummy nibh euismod tincidunt ut laoreet dolore magna aliquam erat volutpat.</p>
    <p class="closing">Sincerely,</p>
    <div class="signature">Dana Wexler</div>
    <p>DW/MQ</p>
  </div>

  <svg class="letter-footer" viewBox="0 0 505 225" role="img" aria-label="Brown speckled paint texture beneath a sweeping gold-edged curve">
    <path d="M0 200 C180 202 380 150 505 0 L505 225 L0 225 Z" fill="var(--brown)"/>
    <path d="M0 200 C180 202 380 150 505 0" fill="none" stroke="var(--gold)" stroke-width="1.6"/>
  </svg>
</section>

<section class="envelope-back">
  <svg class="envelope-flap" viewBox="0 0 537 90" role="img" aria-label="Brown brushed texture across the envelope flap with a gold rule">
    <path d="M0 0 H537 V84 C537 88 533 90 529 90 H8 C4 90 0 88 0 84 Z" fill="var(--brown)"/>
    <rect x="0" y="55" width="537" height="2" fill="var(--gold)"/>
  </svg>
  <div class="seal"><div class="brand-mark"><span class="mark-square"></span><span>Brovanek Data</span></div></div>
</section>

<section class="envelope-front">
  <svg class="front-stripes" viewBox="0 0 535 24" height="24">
    <rect x="0" y="0" width="535" height="13" fill="var(--brown)"/>
    <rect x="0" y="15" width="535" height="2" fill="var(--gold)"/>
    <rect x="0" y="20" width="535" height="2" fill="var(--brown)"/>
  </svg>
  <div class="brand-mark"><span class="mark-square"></span><span>Brovanek Data</span></div>
  <div class="divider"></div>
  <div class="sender">
    <div class="sender-name">Dr. Marla Quenby</div>
    <div>418 Cedar Hollow Road, Ste. 1207</div>
    <div>Pinecrest, TX 76510</div>
    <div>(800) 555-0147</div>
    <div class="sender-email">marla@brovanek-data.com</div>
  </div>
</section>

</body>
</html>
```